Poster for Office

Looking for an edgy, beautiful poster to hang up in my office that uses the quotes located below and potentially the image attached.
Content for poster

Title: Prewitt's Maxims

Must have the following quotes included (punctuation and capitalization are flexible, do what you think looks the best they also don't need the quotation symbols):

"Don't order fish at a steakhouse"
"Be bold. The more you tell, the more you sell"
"admit nothing, deny everything, launch counterattack."
"avoid obviousness"
"never do anything until you're ready to do it"
"look good=feel good"
"always keep the advantage"
"never complain, never explain"
"Lay low, play dumb, keep moving"

Quotes

• Title: Prewitt's Maxims

"avoid obviousness"
"look good=feel good"

```html
<!DOCTYPE html>
<html lang="en">
<head>
<meta charset="utf-8">
<title>Prewitt's Maxims — Office Poster</title>
<link rel="stylesheet" href="https://fonts.googleapis.com/css2?family=Shrikhand&family=Playfair+Display:wght@700&family=Rye&family=Crimson+Text:wght@600&family=Roboto+Condensed:ital,wght@0,300;0,400;1,700&family=Oswald:wght@600&family=Alfa+Slab+One&family=Archivo+Black&family=Lobster+Two:ital,wght@1,700&family=Lobster&family=Ultra&display=swap">
<style>
  :root {
    --page: #ffffff;
    --sepia-light: #cbbbb0;
    --sepia-mid: #9c7a66;
    --sepia-deep: #5a3322;
    --sepia-dark: #1c0d07;
    --ink-light: #ffffff;
  }
  html, body {
    margin: 0;
    padding: 0;
    width: 1200px;
    height: 1000px;
    overflow: hidden;
    background: var(--page);
  }
  .canvas {
    position: relative;
    width: 1200px;
    height: 1000px;
  }
  .poster {
    position: absolute;
    left: 247px;
    top: 0;
    width: 706px;
    height: 1000px;
    overflow: hidden;
  }
  .poster-photo {
    position: absolute;
    inset: 0;
    background:
      radial-gradient(ellipse 70% 45% at 50% 40%, rgba(150,110,90,0.35), rgba(0,0,0,0) 70%),
      linear-gradient(180deg, var(--sepia-light) 0%, #b9a294 30%, var(--sepia-mid) 52%, var(--sepia-deep) 74%, var(--sepia-dark) 100%);
  }
  .poster-type {
    position: absolute;
    left: -247px;
    top: 0;
    width: 1200px;
    height: 1000px;
    fill: var(--ink-light);
  }
  .title       { font-family: "Shrikhand", cursive; font-size: 48px; }
  .rule        { stroke: var(--ink-light); stroke-width: 2; }
  .maxim-fish  { font-family: "Playfair Display", serif; font-weight: 700; font-size: 46px; }
  .maxim-bold  { font-family: "Rye", serif; font-size: 54px; }
  .maxim-tell  { font-family: "Crimson Text", serif; font-weight: 600; font-size: 21px; }
  .maxim-admit { font-family: "Roboto Condensed", sans-serif; font-style: italic; font-weight: 700; font-size: 20px; }
  .maxim-launch{ font-family: "Oswald", sans-serif; font-weight: 600; font-size: 50px; }
  .maxim-avoid { font-family: "Alfa Slab One", serif; font-size: 50px; }
  .maxim-never { font-family: "Archivo Black", sans-serif; font-size: 58px; }
  .maxim-ready { font-family: "Lobster Two", cursive; font-style: italic; font-weight: 700; font-size: 25px; }
  .maxim-look  { font-family: "Roboto Condensed", sans-serif; font-weight: 300; font-size: 44px; }
  .maxim-keep  { font-family: "Roboto Condensed", sans-serif; font-style: italic; font-weight: 400; font-size: 14px; }
  .maxim-adv   { font-family: "Ultra", serif; font-size: 46px; }
  .maxim-complain { font-family: "Lobster", cursive; font-size: 31px; }
  .maxim-lay   { font-family: "Roboto Condensed", sans-serif; font-weight: 400; font-size: 32px; }
</style>
</head>
<body>
<main class="canvas">
  <section class="poster">
    <div class="poster-photo" role="img" aria-label="Sepia photograph of a man's bare back seen from behind, with a portrait tattoo between the shoulder blades, fading to dark brown at the bottom"></div>
    <svg class="poster-type" viewBox="0 0 1200 1000" aria-label="Prewitt's Maxims">
      <text class="title" x="343" y="512" textLength="505" lengthAdjust="spacingAndGlyphs">PREWITT'S MAXIMS</text>
      <line class="rule" x1="343" y1="521" x2="848" y2="521"/>

      <text class="maxim-fish" x="343" y="568" textLength="505" lengthAdjust="spacingAndGlyphs">Dont order fish at a steakhouse</text>

      <text class="maxim-bold" x="343" y="630" textLength="242" lengthAdjust="spacingAndGlyphs">BE BOLD.</text>
      <text class="maxim-tell" x="590" y="600" textLength="258" lengthAdjust="spacingAndGlyphs">THE MORE YOU TELL,</text>
      <text class="maxim-tell" x="590" y="630" textLength="258" lengthAdjust="spacingAndGlyphs">THE MORE YOU SELL</text>

      <text class="maxim-admit" x="343" y="664" textLength="160" lengthAdjust="spacingAndGlyphs">Admit nothing,</text>
      <text class="maxim-admit" x="343" y="691" textLength="160" lengthAdjust="spacingAndGlyphs">Deny everything,</text>
      <text class="maxim-launch" x="507" y="693" textLength="341" lengthAdjust="spacingAndGlyphs">LAUNCH COUNTERATTACK</text>

      <text class="maxim-avoid" x="343" y="748" textLength="505" lengthAdjust="spacingAndGlyphs">AVOID OBVIOUSNESS</text>

      <text class="maxim-never" x="343" y="804" textLength="253" lengthAdjust="spacingAndGlyphs">NEVER</text>
      <text class="maxim-ready" x="604" y="774" textLength="244" lengthAdjust="spacingAndGlyphs">do anything until</text>
      <text class="maxim-ready" x="604" y="803" textLength="244" lengthAdjust="spacingAndGlyphs">you're ready to do it</text>

      <text class="maxim-look" x="343" y="850" textLength="497" lengthAdjust="spacingAndGlyphs">LOOK GOOD = FEEL GOOD</text>

      <text class="maxim-keep" x="343" y="881" textLength="46" lengthAdjust="spacingAndGlyphs">ALWAYS</text>
      <text class="maxim-keep" x="343" y="899" textLength="40" lengthAdjust="spacingAndGlyphs">KEEP</text>
      <text class="maxim-adv" x="420" y="905" textLength="428" lengthAdjust="spacingAndGlyphs">THE ADVANTAGE</text>

      <text class="maxim-complain" x="343" y="943" textLength="497" lengthAdjust="spacingAndGlyphs">Never complain, never explain</text>

      <text class="maxim-lay" x="343" y="985" textLength="505" lengthAdjust="spacingAndGlyphs">LAY LOW, PLAY DUMB, KEEP MOVING</text>
    </svg>
  </section>
</main>
</body>
</html>
```